Business Card for Vorla Parts Wholesale supplier

Hi There! I need a new business card for our company. We are specialized in selling Vorla parts, mostly we sell new LCD screens for Zelnar and Drelks. I would like to see that back in the design.

You can find the colors and logo's on our website: www.hartuvo.nl

Industry/Entity Type

Business

Contact Information for Business Card

My Details:
Tobias Lindqvist

Phone: 0031687203316
E-mail: Tobias@hartuvo.nl

Slogan: "Because Quality Matters"

Font styles to use
Sans Serif

Colors

Designer to choose colors to be used in the design.

Requirements
Must have
• A Black backside with the Hartuvo logo on it. The front side should be clean with only my contact details.
• But I'm also open for something really different or awesome!
Nice to have
• Remember that we are in the parts & repairing industry, So i'll be handing those business cards mainly to repair companies. Maybe you can do something with that thought :)

```html
<!DOCTYPE html>
<html lang="en">
<head>
<meta charset="utf-8">
<title>Hartuvo Business Card</title>
<link rel="stylesheet" href="https://fonts.googleapis.com/css2?family=Ubuntu:wght@400;500;700&display=swap">
<style>
  :root {
    --backdrop: #2b2b2b;
    --card-dark: #303030;
    --card-light: #ffffff;
    --accent: #f07422;
    --ink: #3a3a3a;
    --ink-soft: #555555;
    --on-dark: #ffffff;
  }
  html, body {
    margin: 0;
    padding: 0;
    width: 1200px;
    height: 1000px;
    overflow: hidden;
    background: var(--backdrop);
  }
  .canvas {
    position: relative;
    width: 1200px;
    height: 1000px;
  }
  .card {
    position: absolute;
    left: 240px;
    width: 720px;
    height: 410px;
    border-radius: 28px;
    overflow: hidden;
    box-shadow: 0 12px 30px rgba(0,0,0,0.45);
  }
  .card--back { top: 70px; background: var(--card-dark); }
  .card--front { top: 520px; background: var(--card-light); }
  .card svg { display: block; width: 720px; height: 410px; }
  .brand-name { font-family: 'Ubuntu', sans-serif; font-weight: 700; fill: var(--on-dark); }
  .slogan { font-family: 'Ubuntu', sans-serif; font-weight: 400; font-size: 13px; letter-spacing: 5px; fill: var(--on-dark); }
  .web { font-family: 'Ubuntu', sans-serif; font-weight: 500; font-size: 15px; letter-spacing: 1px; fill: var(--ink); }
  .web-accent, .domain-accent { fill: var(--accent); }
  .domain { font-family: 'Ubuntu', sans-serif; font-size: 15px; letter-spacing: 1px; fill: var(--on-dark); }
  .person-name { font-family: 'Ubuntu', sans-serif; font-weight: 700; font-size: 34px; fill: var(--accent); }
  .person-title { font-family: 'Ubuntu', sans-serif; font-weight: 400; font-size: 19px; fill: var(--ink-soft); }
  .contact { font-family: 'Ubuntu', sans-serif; font-weight: 400; font-size: 17px; fill: var(--ink); }
  .icon { fill: none; stroke: var(--accent); stroke-width: 2.4; stroke-linecap: round; stroke-linejoin: round; }
  .icon-fill { fill: var(--accent); }
</style>
</head>
<body>
<main class="canvas">

  <section class="card card--back" aria-label="Card back">
    <svg viewBox="0 0 720 410">
      <circle class="brand-mark" cx="178" cy="205" r="48" fill="var(--accent)"/>
      <text class="brand-name" x="245" y="238" font-size="100">hartuvo</text>

      <path class="bottom-panel" d="M0 374 H328 C344 374 351 368 359 357 L378 332 C387 320 395 314 412 314 H720 V410 H0 Z" fill="var(--card-light)"/>
      <path class="accent-rule" d="M0 367 H326 C340 367 346 362 353 352 L372 327 C381 315 390 308 410 308" fill="none" stroke="var(--accent)" stroke-width="5"/>

      <text class="slogan" x="40" y="350">"BECAUSE QUALITY MATTERS"</text>
      <text class="web" x="560" y="352">www.<tspan class="web-accent">hartuvo</tspan>.nl</text>
    </svg>
  </section>

  <section class="card card--front" aria-label="Card front">
    <svg viewBox="0 0 720 410">
      <path class="side-panel" d="M0 0 H185 V172 C185 188 188 197 193 208 L268 410 H0 Z" fill="var(--card-dark)"/>
      <path class="accent-rule" d="M196 204 L274 410" fill="none" stroke="var(--accent)" stroke-width="6"/>

      <circle class="brand-mark" cx="88" cy="360" r="32" fill="var(--accent)"/>
      <text class="brand-name" font-size="66" transform="translate(116 310) rotate(-90)">hartuvo</text>
      <text class="domain" transform="translate(146 28) rotate(90)"><tspan class="domain-accent">hartuvo</tspan>.nl</text>

      <text class="person-name" x="245" y="78">Tobias Lindqvist</text>
      <text class="person-title" x="247" y="106">Owner/Producer</text>

      <g class="contact-list">
        <path class="icon" d="M372 281 c0 6 5 11 11 11 l2 -3 -3 -3 -2 1 c-2 -1 -4 -3 -5 -5 l1 -2 -3 -3 z"/>
        <text class="contact" x="398" y="292">0031687203316</text>

        <rect class="icon-fill" x="372" y="305" width="15" height="11" rx="1"/>
        <path d="M372 306 L379.5 312 L387 306" fill="none" stroke="var(--card-light)" stroke-width="1.4"/>
        <text class="contact" x="398" y="317">Tobias@hartuvo.nl</text>

        <circle class="icon" cx="382" cy="335" r="5"/>
        <path class="icon" d="M378 339 L373 344"/>
        <text class="contact" x="398" y="342">www.hartuvo.nl</text>
      </g>
    </svg>
  </section>

</main>
</body>
</html>
```